Vernac Law Business cards and stationary design project

We are looking for a stationary design for business cards (double sided), 8x10, 5x7, and legal and standard envelopes.

We would like the design to match the logo that we have already.
Color palate preferred is Teal, White, grey and any others that will look good for a professional law firm.

We would like this statement: "RELATIONSHIPS. RESPECT. RESULT" to be on the back of the business cards and maybe on the stationary if it looks good.

Please see link to website for more information: www.vernac-law.example

Target Market(s)

Potential clients that need Attorney services.

Industry/Entity Type

Law Firm

Contact Information for Business Card

We would like the front and back to be two different colors. Current business cards are teal front, grey back and are a vertical design. We are open to options with colors.

Font styles to use
Serif

Colors
33a6d7
33b8a4
b9b9b9
5c5c5c

Requirements
Must have
• Logo supplied needs to go on the card and stationary.
• Match website color palate, www.vernac-law.example
• Be professional and not too wordy.
• Criminal Law, Civil Litigation, Personal Injury, Restraining Orders need to be on the card.
Nice to have
• RELATIONSHIPS. RESPECT. RESULTS. on the back of the card.
Should not have
• Not be too busy/wordy or too flashy.

```html
<!DOCTYPE html>
<html lang="en">
<head>
<meta charset="utf-8">
<title>Vernac Law – Business Card</title>
<link href="https://fonts.googleapis.com/css2?family=Cormorant+Garamond:wght@500&family=Source+Sans+3:ital,wght@0,400;0,600;1,400&display=swap" rel="stylesheet">
<style>
  :root {
    --backdrop: #3b3432;
    --card: #141414;
    --card-edge: #1f1f1f;
    --teal: #1f8e98;
    --teal-bright: #33b8c4;
    --white: #f2f2f2;
    --silver: #b9b9b9;
    --divider: #5c5c5c;
  }
  * { box-sizing: border-box; margin: 0; padding: 0; }
  html, body { width: 1200px; height: 814px; overflow: hidden; }
  body {
    background: var(--backdrop);
    font-family: "Source Sans 3", "Helvetica Neue", Arial, sans-serif;
    position: relative;
  }
  .card {
    position: absolute;
    width: 520px;
    height: 297px;
    background: var(--card);
    border: 1px solid var(--card-edge);
    box-shadow: 0 14px 30px rgba(0,0,0,.45);
  }
  .card--front { left: 60px; top: 258px; }
  .card--back { left: 620px; top: 258px; }

  /* Front */
  .front__brand {
    position: absolute;
    left: 34px; top: 92px;
    width: 180px;
    text-align: center;
    font-family: "Cormorant Garamond", Georgia, serif;
    font-weight: 500;
    font-size: 34px;
    line-height: 1.1;
    color: var(--teal);
  }
  .front__divider {
    position: absolute;
    left: 232px; top: 50px;
    width: 1px; height: 130px;
    background: var(--divider);
  }
  .front__contact {
    position: absolute;
    left: 256px; top: 54px;
    color: var(--white);
  }
  .contact__name {
    font-size: 19px;
    font-weight: 600;
    color: var(--teal-bright);
    line-height: 1.1;
  }
  .contact__role { font-size: 14px; margin-bottom: 10px; }
  .contact__list { list-style: none; font-size: 14px; }
  .contact__item {
    display: flex;
    align-items: center;
    gap: 9px;
    margin-bottom: 5px;
  }
  .contact__icon { width: 12px; height: 12px; fill: var(--teal-bright); flex: none; }
  .front__services {
    position: absolute;
    left: 30px; right: 20px; bottom: 30px;
    font-size: 15px;
    font-style: italic;
    color: var(--white);
    letter-spacing: .2px;
  }

  /* Back */
  .back__inner {
    position: absolute;
    inset: 0;
    display: flex;
    flex-direction: column;
    align-items: center;
    justify-content: center;
  }
  .back__brand {
    font-family: "Cormorant Garamond", Georgia, serif;
    font-weight: 500;
    font-size: 30px;
    letter-spacing: 3px;
    text-transform: uppercase;
    color: var(--silver);
  }
  .back__rule {
    width: 150px; height: 1px;
    background: var(--divider);
    margin: 12px 0 40px;
  }
  .back__tagline {
    font-size: 14px;
    font-weight: 600;
    letter-spacing: 1px;
    color: var(--teal-bright);
  }
</style>
</head>
<body>
  <section class="card card--front" aria-label="Business card front">
    <div class="front__brand">Vernac Law</div>
    <div class="front__divider"></div>
    <div class="front__contact">
      <p class="contact__name">Daniel Marsh</p>
      <p class="contact__role">CEO/Founder</p>
      <ul class="contact__list">
        <li class="contact__item">
          <svg class="contact__icon" viewBox="0 0 12 12" aria-hidden="true"><path d="M2.5 0.5l2 2.4-1.2 1.3c.6 1.6 1.9 2.9 3.5 3.5l1.3-1.2 2.4 2-1.2 2.5C4.8 10.7 1.3 7.2 0 2.7z"/></svg>
          <span>555 014 2270</span>
        </li>
        <li class="contact__item">
          <svg class="contact__icon" viewBox="0 0 12 12" aria-hidden="true"><path d="M0 2h12v8H0z M1 3l5 3.5L11 3v-.2H1z" fill-rule="evenodd"/></svg>
          <span>info@vernac-law.example</span>
        </li>
        <li class="contact__item">
          <svg class="contact__icon" viewBox="0 0 12 12" aria-hidden="true"><circle cx="6" cy="6" r="6"/><path d="M1 6h10M6 0.5c-2.2 2.8-2.2 8.2 0 11M6 0.5c2.2 2.8 2.2 8.2 0 11" stroke="#141414" stroke-width=".9" fill="none"/></svg>
          <span>www.vernac-law.example</span>
        </li>
      </ul>
    </div>
    <p class="front__services">Criminal Law,&nbsp; Civil Litigation/Personal Injury , Restraining Orders</p>
  </section>

  <section class="card card--back" aria-label="Business card back">
    <div class="back__inner">
      <div class="back__brand">Vernac Law</div>
      <div class="back__rule"></div>
      <p class="back__tagline">RELATIONSHIPS. RESPECT. RESULTS</p>
    </div>
  </section>
</body>
</html>
```